Web Site Design for a Finance (lending) Company

We are opening a new subsidiary that focuses on lending money in the real estate industry. We need a web site designed to represent the business.

The business is lending money to real estate investors. A typical client/borrower will be looking to borrow money to buy a house, renovate it and then sell it at a profit, all within 12 months or less.

Company name is RTV Finance. Our logo is attached.

Attached is a general outline for the web site. We're working on writing more text for each page but this should give you enough to get started with some ideas.

Competitor web site that I like a lot (as an example): https://dorvaleqcapital.example/. Many of the general items on this site match what we will need (description of loan programs, FAQ)

Target Market(s)

Real estate investors (generally individuals or small companies with just a few people) who are buying homes, renovating them and then selling them at a profit.

Industry/Entity Type

Finance

Coding

Coded - Design and coding required

Number of Pages Required

5+ page

Colors

Designer to choose colors to be used in the design.

Requirements
Must have
• Minimalist design. Clean lines without too much clutter. Some stock photography is ok but the photos should not be distracting. They should almost fade in to the background so that user can focus on the key information about what our company does instead. We are a finance company, not a design company, so the information about our products will be more interesting to site visitors than the art.
• Some minimalist examples from Snapboard:
• https://www.snapboardia.example/explore/minimalist-web-design/
Nice to have
• If you search in zoovle for "hard money lenders" you will find many examples of web sites from our competition. I have provided a link above to competitor web site that I like a lot.
• I have attached our logo in EPS format. Logo is green. Web site doesn't have to be green but it should be of a color that will work well with the logo.

```html
<!DOCTYPE html>
<html lang="en">
<head>
<meta charset="utf-8">
<title>RTV Finance</title>
<link rel="stylesheet" href="https://fonts.googleapis.com/css2?family=Open+Sans:wght@400;600;700&family=Roboto:wght@400;500;700&display=swap">
<style>
:root{
  --green:#0b4a31;
  --green-dark:#08361f;
  --ink:#1d1d1d;
  --muted:#6b6b6b;
  --light:#efefef;
  --line:#d8d8d8;
  --footer:#6e6e6e;
  --white:#ffffff;
}
*{box-sizing:border-box;margin:0;padding:0}
html,body{width:1200px;height:3130px;overflow:hidden}
body{font-family:"Open Sans",Arial,sans-serif;color:var(--ink);background:var(--white);position:relative}
section,header,footer{position:relative;width:1200px}

/* header */
.site-header{height:108px;border-top:6px solid var(--green);background:var(--white)}
.login-tab{position:absolute;right:0;top:-6px;width:250px;height:26px;background:var(--green);clip-path:polygon(8% 0,100% 0,100% 100%,0 100%);color:var(--white);font:600 14px "Open Sans",sans-serif;display:flex;align-items:center;justify-content:flex-end;padding-right:62px;gap:8px}
.brand{position:absolute;left:100px;top:26px;display:flex;align-items:center;gap:12px;font:700 30px "Roboto",sans-serif;color:var(--green)}
.brand-mark{width:44px;height:44px;background:var(--green)}
.main-nav{position:absolute;right:80px;top:52px;display:flex;gap:40px;font:600 15px "Open Sans",sans-serif;color:#222}
.main-nav .active{color:var(--green)}
.caret::after{content:" \2304";font-size:11px}

/* hero */
.hero{height:407px;background:linear-gradient(180deg,#9fb0bf 0%,#b9b4a6 45%,#6f8a52 78%,#4f6b33 100%)}
.hero-text{position:absolute;top:140px;width:100%;text-align:center;color:var(--white);font:700 44px/56px "Roboto",sans-serif;text-shadow:0 2px 6px rgba(0,0,0,.45)}
.hero-btn{position:absolute;left:525px;top:273px;width:152px;height:46px;border-radius:8px;background:var(--green);color:var(--white);font:600 14px "Open Sans",sans-serif;display:flex;align-items:center;justify-content:center}
.hero-arrow{position:absolute;top:170px}

/* who */
.who{height:460px}
.section-title{font:600 31px "Roboto",sans-serif;color:var(--ink)}
.who .section-title{position:absolute;left:98px;top:102px}
.who p{position:absolute;left:98px;width:430px;font:400 13.5px/22px "Open Sans",sans-serif;color:var(--muted)}
.btn-solid{position:absolute;background:var(--green);color:var(--white);font:600 14px "Open Sans",sans-serif;border-radius:8px;display:flex;align-items:center;justify-content:center}
.who-photo{position:absolute;left:595px;top:73px;width:505px;height:318px;border:2px solid #cfd6cf;background:linear-gradient(135deg,#f3f3f0 0%,#e6e4dd 55%,#7a5a3c 100%)}

/* why */
.why{height:590px;background:var(--light)}
.why-photo{position:absolute;left:100px;top:130px;width:305px;height:305px;border-radius:50%;border:6px solid var(--white);background:radial-gradient(circle at 50% 40%,#a9b8a0 0%,#6f7a5a 55%,#3b3326 100%)}
.why .section-title{position:absolute;left:500px;top:58px}
.why-lede{position:absolute;left:500px;top:120px;width:580px;font:400 13.5px/22px "Open Sans",sans-serif;color:var(--muted)}
.feature{position:absolute;width:190px;display:flex;flex-direction:column;align-items:flex-start;gap:10px;font:500 18px "Roboto",sans-serif;color:var(--ink)}
.feature svg{stroke:var(--green);fill:none;stroke-width:2.2}
.btn-outline{position:absolute;left:498px;top:465px;width:153px;height:50px;border:1.5px solid var(--green);border-radius:8px;color:var(--green-dark);font:600 14px "Open Sans",sans-serif;display:flex;align-items:center;justify-content:center;background:var(--white)}

/* lending band */
.lending{height:418px;background:linear-gradient(90deg,#1c2b26 0%,#2b3b35 50%,#1d2a25 100%);color:var(--white);text-align:center}
.lending h2{position:absolute;top:88px;width:100%;font:500 33px "Roboto",sans-serif}
.lending p{position:absolute;left:220px;width:760px;font:600 17px/24px "Open Sans",sans-serif}
.btn-ghost{position:absolute;left:515px;top:286px;width:168px;height:46px;border:2px solid var(--white);border-radius:8px;font:600 14px "Open Sans",sans-serif;display:flex;align-items:center;justify-content:center}

/* loans */
.loans{height:490px}
.loans .section-title{position:absolute;top:96px;width:100%;text-align:center}
.loan-card{position:absolute;top:162px;width:482px;height:276px;border:1.5px solid var(--line);border-radius:6px;background:var(--white)}
.loan-inner{position:absolute;left:8px;top:8px;right:8px;bottom:8px;background:var(--light);display:flex}
.loan-photo{flex:0 0 255px;width:255px;height:100%}
.loan-body{flex:1 1 auto;padding:48px 16px 0 18px}
.loan-body h3{font:700 18px "Roboto",sans-serif;margin-bottom:10px}
.loan-body p{font:400 13.5px/22px "Open Sans",sans-serif;color:var(--muted);margin-bottom:6px}
.loan-body a{font:700 14px "Open Sans",sans-serif;color:var(--green);text-decoration:none}
.divider{position:absolute;left:98px;right:98px;bottom:0;height:3px;background:#cfcfcf}

/* partners */
.partners{height:288px}
.partners .section-title{position:absolute;top:80px;width:100%;text-align:center;font-size:27px}
.partner-row{position:absolute;left:96px;top:148px;display:flex;gap:16px}
.partner-badge{width:188px;height:61px;border:1.5px solid var(--line);display:flex;align-items:center;justify-content:center}
.partner-badge span{width:110px;height:22px;background:#d9d9d9;border-radius:3px}

/* footer */
.site-footer{height:333px;background:var(--footer);color:var(--white)}
.newsletter{position:absolute;left:96px;top:-36px;width:1004px;height:70px;background:var(--green);display:flex;align-items:center;padding-left:92px}
.newsletter h4{font:500 25px "Roboto",sans-serif}
.newsletter-field{position:absolute;left:542px;top:15px;width:378px;height:38px;background:var(--white);border-radius:8px}
.newsletter-btn{position:absolute;right:0;top:0;height:38px;width:100px;background:var(--green);border:2px solid var(--white);border-radius:8px;font:700 13px "Open Sans",sans-serif;display:flex;align-items:center;justify-content:center}
.footer-brand{position:absolute;left:125px;top:120px;display:flex;align-items:center;gap:12px;font:500 30px "Roboto",sans-serif}
.footer-brand .brand-mark{background:var(--white);width:40px;height:40px}
.footer-col{position:absolute;top:85px}
.footer-col h5{font:700 15px "Roboto",sans-serif;margin-bottom:14px;letter-spacing:.3px}
.footer-col li{list-style:none;font:400 13px/27px "Open Sans",sans-serif}
.contact li{display:flex;align-items:center;gap:8px}
.socials{display:flex;gap:12px;margin-top:8px}
.socials span{width:22px;height:22px;border:1.5px solid #9a9a9a;transform:rotate(45deg);background:#5f5f5f}
.copyright{position:absolute;top:300px;width:100%;text-align:center;font:400 13px "Open Sans",sans-serif}
.footer-rule{position:absolute;left:440px;right:96px;top:278px;height:1px;background:#8a8a8a}
.chat{position:absolute;left:1045px;top:220px;width:54px;height:54px;border-radius:50%;background:var(--white);display:flex;align-items:center;justify-content:center}
</style>
</head>
<body>

<header class="site-header">
  <div class="login-tab">
    <svg width="14" height="14" viewBox="0 0 14 14"><circle cx="7" cy="4" r="3" fill="#fff"/><path d="M1 14c0-4 3-6 6-6s6 2 6 6z" fill="#fff"/></svg>
    Login
  </div>
  <div class="brand"><span class="brand-mark"></span>RTV Finance</div>
  <nav class="main-nav">
    <span class="active">Home</span>
    <span class="caret">About Us</span>
    <span class="caret">Loans</span>
    <span class="caret">Resources</span>
    <span>Contact Us</span>
    <svg width="16" height="16" viewBox="0 0 16 16" fill="none" stroke="#222" stroke-width="2.2"><circle cx="6.5" cy="6.5" r="5"/><path d="M10.5 10.5L15 15"/></svg>
  </nav>
</header>

<section class="hero" role="img" aria-label="Suburban family house with front lawn and trees">
  <svg class="hero-arrow" style="left:24px" width="30" height="46" viewBox="0 0 30 46" fill="none" stroke="#fff" stroke-width="4"><path d="M26 4L6 23l20 19"/></svg>
  <svg class="hero-arrow" style="right:24px" width="30" height="46" viewBox="0 0 30 46" fill="none" stroke="#fff" stroke-width="4"><path d="M4 4l20 19L4 42"/></svg>
  <div class="hero-text">Local Real Estate Experts Lending To<br>Local Real Estate Investors</div>
  <div class="hero-btn">LEARN MORE</div>
</section>

<section class="who">
  <h2 class="section-title">WHO WE ARE ?</h2>
  <p style="top:160px">RTV Finance is a local business with local knowledge and strong industry relationships. A partner with a wide network who offers value added services.</p>
  <p style="top:244px">RTV has an established pool of experienced investors available for your real estate investment needs</p>
  <div class="btn-solid" style="left:98px;top:320px;width:150px;height:48px">READ MORE</div>
  <div class="who-photo" role="img" aria-label="Model house and pen resting on a loan document"></div>
</section>

<section class="why">
  <div class="why-photo" role="img" aria-label="Stacks of coins growing from soil under a house outline with a rising arrow"></div>
  <h2 class="section-title">WHY BORROW FROM RTV ?</h2>
  <p class="why-lede">RTV Finance is a local business with local knowledge and strong industry relationships. A partner with a wide network who offers value added services.</p>

  <div class="feature" style="left:508px;top:195px">
    <svg width="62" height="60" viewBox="0 0 62 60"><path d="M31 3l8 18 19 2-14 13 4 19-17-10-17 10 4-19L4 23l19-2z"/></svg>Experts
  </div>
  <div class="feature" style="left:668px;top:195px">
    <svg width="62" height="60" viewBox="0 0 62 60"><path d="M8 26h10v30H8zM18 28l10-12 4-12c4 0 7 3 6 9l-3 9h17c4 0 6 4 4 7 2 2 2 5-1 7 2 2 1 5-2 6 1 3-1 6-5 6H18"/></svg>Fast Approval
  </div>
  <div class="feature" style="left:866px;top:195px">
    <svg width="62" height="60" viewBox="0 0 62 60"><circle cx="31" cy="18" r="11"/><path d="M22 12h18M8 58c0-14 10-22 23-22s23 8 23 22zM31 36v22M27 40l4 6 4-6"/></svg>Professional
  </div>
  <div class="feature" style="left:498px;top:330px">
    <svg width="88" height="60" viewBox="0 0 88 60"><path d="M3 14h12v28H3zM73 14h12v28H73zM15 18h14l10-4 14 4h20M15 38h8l12 10c3 2 6 0 5-3l5 4c3 1 5-1 4-4l4 3c3 1 5-2 3-5l3 1c3 0 4-3 2-5L60 22l-10 6c-4 2-8 0-6-4"/></svg>A Partner
  </div>
  <div class="feature" style="left:690px;top:330px">
    <svg width="62" height="60" viewBox="0 0 62 60"><circle cx="31" cy="30" r="25"/><path d="M19 31l8 8 17-18"/></svg>Selective
  </div>
  <div class="feature" style="left:840px;top:330px">
    <svg width="62" height="60" viewBox="0 0 62 60"><rect x="6" y="10" width="44" height="26" rx="2"/><circle cx="28" cy="23" r="6"/><rect x="14" y="26" width="44" height="26" rx="2"/><circle cx="36" cy="39" r="6"/></svg>Competative fees
  </div>
  <div class="btn-outline">READ MORE</div>
</section>

<section class="lending" role="img" aria-label="Adviser meeting with clients, softly darkened behind text">
  <h2>We Are Lending Money To Real Estate Investors</h2>
  <p style="top:152px">RTV Finance is a local business with local knowledge and strong industry relationships. A partner with a wide network who offers value added services.</p>
  <p style="top:212px;left:270px;width:660px">RTV has an established pool of experienced investors available for your real estate investment needs</p>
  <div class="btn-ghost">GET CONNECTED !</div>
</section>

<section class="loans">
  <h2 class="section-title">LOANS OFFERED</h2>
  <article class="loan-card" style="left:96px">
    <div class="loan-inner">
      <div class="loan-photo" role="img" aria-label="Homeowner holding a small model house and a paint roller" style="background:linear-gradient(135deg,#e9e7e2 0%,#c9a98a 50%,#8fb79a 100%)"></div>
      <div class="loan-body">
        <h3>Flip And Fix Loans</h3>
        <p>We established pool of experienced investors available for your real estate investment needs</p>
        <a>Read More &raquo;</a>
      </div>
    </div>
  </article>
  <article class="loan-card" style="left:618px">
    <div class="loan-inner">
      <div class="loan-photo" role="img" aria-label="Rising growth arrow over city buildings" style="background:linear-gradient(135deg,#ece9d8 0%,#c9c07a 50%,#6e6a36 100%)"></div>
      <div class="loan-body">
        <h3>Commercial Loans</h3>
        <p>We established pool of experienced investors available for your real estate investment needs</p>
        <a>Read More &raquo;</a>
      </div>
    </div>
  </article>
  <div class="divider"></div>
</section>

<section class="partners">
  <h2 class="section-title">OUR PARTNERS</h2>
  <div class="partner-row">
    <div class="partner-badge"><span></span></div>
    <div class="partner-badge"><span></span></div>
    <div class="partner-badge"><span></span></div>
    <div class="partner-badge"><span></span></div>
    <div class="partner-badge"><span></span></div>
  </div>
</section>

<footer class="site-footer">
  <div class="newsletter">
    <h4>SUBSCRIBE FOR NEWSLETTER</h4>
    <div class="newsletter-field"><div class="newsletter-btn">SUBMIT</div></div>
  </div>
  <div class="footer-brand"><span class="brand-mark"></span>RTV Finance</div>
  <div class="footer-col" style="left:449px">
    <h5>USEFUL LINKS</h5>
    <ul><li>Home</li><li>About Us</li><li>Loans</li><li>Resources</li><li>Contact Us</li></ul>
  </div>
  <div class="footer-col contact" style="left:668px">
    <h5>CONTACT US</h5>
    <ul>
      <li><svg width="10" height="14" viewBox="0 0 10 14"><path d="M5 0a5 5 0 015 5c0 4-5 9-5 9S0 9 0 5a5 5 0 015-5z" fill="#1f7a4d"/></svg>E-27, Dorset Lane, 000412</li>
      <li><svg width="12" height="12" viewBox="0 0 12 12"><path d="M2 0l3 3-2 2c1 2 2 3 4 4l2-2 3 3-2 2C5 12 0 7 0 2z" fill="#1f7a4d"/></svg>555 214 7730</li>
      <li><svg width="13" height="10" viewBox="0 0 13 10"><rect width="13" height="10" fill="#1f7a4d"/><path d="M0 0l6.5 5L13 0" stroke="#6e6e6e" fill="none"/></svg>info@rtvfinance.example</li>
    </ul>
  </div>
  <div class="footer-col" style="left:945px">
    <h5>SOCIAL LINKS</h5>
    <div class="socials"><span></span><span></span><span></span><span></span></div>
  </div>
  <div class="chat">
    <svg width="30" height="28" viewBox="0 0 30 28"><path d="M3 2h24v17H12l-6 6v-6H3z" fill="#0b4a31"/></svg>
  </div>
  <div class="footer-rule"></div>
  <div class="copyright">Copyright &copy; 2017 RTV Finance. All Rights Reserved.</div>
</footer>

</body>
</html>
```